Tavoria canola oil needs a lable design

We need to design a label for our TAVORIA brand canola oil. We want our product to be easily noticed on supermarket shelves and clearly identified as Australian-made, distinguishing it from other canola oils. Our product is 100% Australian-made, non-GMO canola oil. The packaging size is 2 liters. The front and back label designs are required.
Updates

The label needs to be advanced, high-class and eye-catching. The Logo is just a reference and can be redesigned if there is a better idea.

I invited a new designer to create a design on Monday, but I haven't received the design work yet. I'm worried that my time might have expired and that he wasn't able to upload it.

Target Market(s)

high-end supermarket

Industry/Entity Type

cold pressed canola oil

Requirements
Must have
• 100% Australian-made,non-GMO,nutrition board,Kosher certification,Halal certification,HACCP
Nice to have
• easily be noticed at supermarket and clearly identified as Australian-made;different from the existing canola oil label design

```html
<!DOCTYPE html>
<html lang="en">
<head>
<meta charset="utf-8">
<title>Tavoria Canola Oil – Front and Back Labels</title>
<link rel="stylesheet" href="https://fonts.googleapis.com/css2?family=Nunito:wght@900&family=Open+Sans:wght@300;400;600&family=Playfair+Display:wght@900&family=Archivo+Black&family=Roboto:wght@400;700&display=swap">
<style>
  :root {
    --page: #ffffff;
    --navy: #13286a;
    --title-yellow: #ffd51f;
    --title-edge: #6b4a00;
    --white: #ffffff;
    --ink: #111111;
    --rule: #999999;
    --back-top: #e9ee6a;
    --back-mid: #b9cf3a;
    --back-low: #8fb22c;
    --badge: #f4f4f4;
    --badge-ring: #222222;
  }
  * { box-sizing: border-box; margin: 0; padding: 0; }
  html, body { width: 999px; height: 1200px; overflow: hidden; background: var(--page); }
  .canvas { position: relative; width: 999px; height: 1200px; }

  .label {
    position: absolute; top: 187px; width: 430px; height: 825px;
    border-radius: 9px; overflow: hidden;
  }
  .label--front { left: 49px; background: var(--navy); }
  .label--back { left: 519px; background: linear-gradient(180deg, var(--back-top) 0%, var(--back-mid) 55%, var(--back-low) 100%); }

  .front-art { position: absolute; inset: 0; }
  .flag-area { position: absolute; left: 0; top: 0; width: 206px; height: 99px; background: linear-gradient(135deg, #c8102e 0%, #ffffff 45%, #1a2d6e 100%); }
  .kangaroo-area { position: absolute; left: 101px; top: 176px; width: 180px; height: 128px; border-radius: 50% 40% 45% 30%; background: linear-gradient(160deg, #ffffff 0%, #dfeaf4 100%); opacity: .92; }

  .gmo-free {
    position: absolute; left: 300px; top: 283px; width: 110px;
    font-family: "Playfair Display", serif; font-weight: 900; font-size: 30px; line-height: 26px;
    color: var(--white); text-align: right; letter-spacing: 1px;
  }
  .product-title {
    position: absolute; left: 0; right: 0;
    font-family: "Nunito", sans-serif; font-weight: 900; color: var(--title-yellow);
    text-align: center; letter-spacing: -1px;
    text-shadow: 2px 2px 0 var(--title-edge), -1px -1px 0 var(--title-edge), 1px -1px 0 var(--title-edge), -1px 1px 0 var(--title-edge);
  }
  .label--front .product-title { top: 355px; font-size: 58px; }
  .label--back .product-title { top: 30px; font-size: 54px; }

  .brand-mark {
    position: absolute; left: 134px; top: 535px; width: 160px; height: 160px;
    border-radius: 50%; background: var(--white);
    display: flex; align-items: center; justify-content: center;
  }
  .brand-name { font-family: "Open Sans", sans-serif; font-weight: 600; font-size: 28px; letter-spacing: 2px; color: var(--ink); }

  .certifications { position: absolute; left: 19px; top: 731px; display: flex; gap: 10px; }
  .cert-badge { width: 68px; height: 68px; border-radius: 50%; background: var(--badge); border: 4px solid var(--badge-ring); }
  .volume {
    position: absolute; right: 22px; top: 746px;
    font-family: "Open Sans", sans-serif; font-weight: 400; font-size: 33px; color: var(--white);
  }

  .back-art { position: absolute; left: 0; bottom: 0; width: 430px; height: 240px;
    background: linear-gradient(180deg, rgba(242,212,25,0) 0%, #f2d419 30%, #1f3f9a 60%, #13286a 100%); }
  .oil-jug-area { position: absolute; right: 10px; top: 470px; width: 88px; height: 150px; border-radius: 30px 30px 40px 40px; background: linear-gradient(180deg, #f3ea8c 0%, #f1c40f 100%); }

  .nutrition {
    position: absolute; left: 56px; top: 115px; width: 311px;
    background: var(--white); border: 2px solid var(--ink); padding: 3px 5px 6px;
    font-family: "Roboto", sans-serif; color: var(--ink); font-size: 13px;
  }
  .nutrition__title { font-family: "Archivo Black", sans-serif; font-size: 35px; line-height: 38px; letter-spacing: .5px; }
  .nutrition__row { display: flex; justify-content: space-between; align-items: flex-end; height: 19px; border-top: 1px solid var(--rule); }
  .nutrition__row--serving { border: 0; font-weight: 700; font-size: 16px; height: 22px; }
  .nutrition__row--first { border-top: 0; }
  .bar-thick { height: 7px; background: var(--ink); margin: 2px 0; }
  .bar-mid { height: 4px; background: var(--ink); margin: 2px 0; }
  .nutrition__amount { font-weight: 700; font-size: 13px; padding-top: 2px; }
  .nutrition__calories { display: flex; justify-content: space-between; align-items: flex-end; font-family: "Archivo Black", sans-serif; }
  .nutrition__calories .name { font-size: 25px; line-height: 28px; }
  .nutrition__calories .value { font-size: 37px; line-height: 38px; }
  .nutrition__dv { text-align: right; font-size: 10px; font-weight: 700; height: 16px; }
  .nutrition__row b { font-weight: 700; }
  .nutrition__row .pct { font-weight: 700; }
  .nutrition__row--sub { padding-left: 18px; }
  .nutrition__row--subsub { padding-left: 36px; }
  .nutrition__row--mineral .pct { font-weight: 400; }
  .nutrition__note { font-size: 10px; line-height: 12px; padding: 3px 4px 0; }
</style>
</head>
<body>
<main class="canvas">

  <section class="label label--front" aria-label="Front label">
    <svg class="front-art" width="430" height="825" viewBox="0 0 430 825">
      <defs>
        <linearGradient id="landscape" x1="0" y1="0" x2="0" y2="1">
          <stop offset="0" stop-color="#4aa6e6"/>
          <stop offset="0.33" stop-color="#cfe3ee"/>
          <stop offset="0.42" stop-color="#5f7f9c"/>
          <stop offset="0.5" stop-color="#b9a760"/>
          <stop offset="0.6" stop-color="#5e8a3a"/>
          <stop offset="0.72" stop-color="#f2d419"/>
          <stop offset="1" stop-color="#e8c414"/>
        </linearGradient>
        <path id="made-arc" d="M200,168 C270,175 330,205 425,228"/>
      </defs>
      <path role="img" aria-label="Photo of a blue sky over hills and a flowering yellow canola field"
            d="M0,265 C60,250 110,212 160,206 C240,200 320,250 430,244 L430,825 L0,825 Z" fill="url(#landscape)"/>
      <text font-family="Open Sans, sans-serif" font-size="19" fill="#ffffff" letter-spacing="1">
        <textPath href="#made-arc">100% Australian-made</textPath>
      </text>
    </svg>
    <div class="flag-area" role="img" aria-label="Australian flag with Union Jack and Southern Cross stars"></div>
    <div class="kangaroo-area" role="img" aria-label="White leaping kangaroo illustration"></div>
    <div class="gmo-free">GMO<br>FREE</div>
    <h1 class="product-title">CANOLA OIL</h1>
    <div class="brand-mark"><span class="brand-name">TAVORIA</span></div>
    <div class="certifications" aria-label="Kosher, Halal and HACCP certifications">
      <span class="cert-badge"></span>
      <span class="cert-badge"></span>
      <span class="cert-badge"></span>
    </div>
    <div class="volume">2 liters</div>
  </section>

  <section class="label label--back" aria-label="Back label">
    <h2 class="product-title">CANOLA OIL</h2>
    <div class="back-art" role="img" aria-label="Illustration of canola flowers, seeds and a waving Australian flag"></div>
    <div class="oil-jug-area" role="img" aria-label="Glass jug of golden canola oil"></div>
    <div class="nutrition">
      <div class="nutrition__title">Nutrition Facts</div>
      <div class="nutrition__row nutrition__row--serving"><span>Serving size</span><span>(100g)</span></div>
      <div class="bar-thick"></div>
      <div class="nutrition__amount">Amount Per Serving</div>
      <div class="nutrition__calories"><span class="name">Calories</span><span class="value">380</span></div>
      <div class="bar-mid"></div>
      <div class="nutrition__dv">% Daily Value*</div>
      <div class="nutrition__row"><span><b>Total Fat</b> 6g</span><span class="pct">8%</span></div>
      <div class="nutrition__row nutrition__row--sub"><span>Saturated Fat 0g</span><span class="pct">0%</span></div>
      <div class="nutrition__row nutrition__row--sub"><span><i>Trans</i> Fat 0g</span><span></span></div>
      <div class="nutrition__row"><span><b>Cholesterol</b> 0mg</span><span class="pct">0%</span></div>
      <div class="nutrition__row"><span><b>Sodium</b> 0mg</span><span class="pct">0%</span></div>
      <div class="nutrition__row"><span><b>Total Carbohydrate</b> 62g</span><span class="pct">23%</span></div>
      <div class="nutrition__row nutrition__row--sub"><span>Dietary Fiber 5g</span><span class="pct">18%</span></div>
      <div class="nutrition__row nutrition__row--sub"><span>Total Sugars 0g</span><span></span></div>
      <div class="nutrition__row nutrition__row--subsub"><span>Includes 0g Added Sugars</span><span class="pct">0%</span></div>
      <div class="nutrition__row"><span><b>Protein</b> 14g</span><span class="pct">28%</span></div>
      <div class="bar-thick"></div>
      <div class="nutrition__row nutrition__row--mineral nutrition__row--first"><span>Vitamin D 0mcg</span><span class="pct">0%</span></div>
      <div class="nutrition__row nutrition__row--mineral"><span>Calcium 52mg</span><span class="pct">4%</span></div>
      <div class="nutrition__row nutrition__row--mineral"><span>Iron 6.03mg</span><span class="pct">35%</span></div>
      <div class="nutrition__row nutrition__row--mineral"><span>Potassium 1043mg</span><span class="pct">20%</span></div>
      <div class="bar-mid"></div>
      <p class="nutrition__note">*The % Daily Value (DV) tells you how much a nutrient in a serving of food contributes to a daily diet. 2,000 calories a day is used for general nutrition advice.</p>
    </div>
  </section>

</main>
</body>
</html>
```